Informational Site for Advanced Chemistry R&D

The company develops oxidation chemistry for air, water, fuel pollution controls. The site has been prototyped at www.velquaresearch.example. Take a look. Now, the task is to design it for eye-catching beauty with use of color, on-page scroll-driven color transition and parallax effects. Should capture the themes: high technology, wow it's beautiful, modern, uncluttered, clean urban environment.

Target Market(s)

China Environmentally Conscious Government and Industry,

Industry/Entity Type

It Company

Number of Pages Required

3 page

Font styles to use
Sans Serif

Requirements
Must have
• Parallax effects, desktop compatible, Rich, Modern, Simple, Graphic
Nice to have
• Mobile Phone Compatible
Should not have
• Flash, or anything that is slow to load or requires high bandwidth

```html
<!DOCTYPE html>
<html lang="en">
<head>
<meta charset="utf-8">
<title>Velquara – Advanced Oxidation Science</title>
<link rel="stylesheet" href="https://fonts.googleapis.com/css2?family=Montserrat:wght@400;600;700&family=Open+Sans:wght@400;600;700&display=swap">
<style>
:root{
  --blue:#1a6fb6;
  --blue-dark:#15609f;
  --teal:#2cb5b0;
  --ink:#333;
  --muted:#666;
  --light:#f2f2f2;
  --navy:#1d2140;
  --footer:#1e1e1e;
  --footer-deep:#121212;
  --field:#333;
  --white:#fff;
}
*{box-sizing:border-box;margin:0;padding:0}
html,body{width:1200px;height:3087px;overflow:hidden}
body{position:relative;font-family:"Open Sans",Arial,sans-serif;color:var(--ink);background:var(--white)}
.abs{position:absolute}
.head{font-family:"Montserrat",Arial,sans-serif}

/* hero */
.hero{left:0;top:0;width:1200px;height:614px;overflow:hidden}
.hero-photo{position:absolute;inset:0;background:linear-gradient(180deg,#f4f5f6 0%,#dfe3e6 30%,#a9b4bb 55%,#6f7d86 75%,#8c9aa2 100%)}
.hero-brand{left:0;width:1200px;top:118px;text-align:center;font-family:"Montserrat",sans-serif;font-weight:600;font-size:34px;color:var(--blue)}
.hero-brand .dot{display:inline-block;width:64px;height:64px;border-radius:50%;background:var(--blue);position:absolute;left:568px;top:-90px}
.hero-title{left:0;width:1200px;top:268px;text-align:center}
.hero-title span{display:inline-block;background:rgba(30,30,30,.82);color:var(--white);font-family:"Montserrat",sans-serif;font-weight:700;font-size:33px;letter-spacing:.5px;padding:2px 12px;margin-bottom:6px;line-height:42px}
.hero-arrow{top:316px;width:38px;height:38px;border-radius:50%;background:rgba(255,255,255,.3)}

/* nav */
.nav{left:0;top:614px;width:1200px;height:86px;background:var(--blue)}
.nav-mark{left:100px;top:24px;width:38px;height:38px;border-radius:50%;border:3px solid var(--white)}
.nav-menu{left:0;top:0;height:86px;width:1200px}
.nav-menu a{position:absolute;top:33px;color:var(--white);text-decoration:none;font-family:"Montserrat",sans-serif;font-weight:600;font-size:14px}
.nav-sep{left:1053px;top:24px;width:1px;height:38px;background:rgba(255,255,255,.35)}

/* intro */
.intro{left:0;top:700px;width:1200px;height:335px;background:var(--light)}
.intro-brand{left:120px;top:160px;width:330px;text-align:center;font-family:"Montserrat",sans-serif;font-size:46px;font-weight:600;color:#c4c4c4}
.intro-brand .dot{position:absolute;left:130px;top:-120px;width:76px;height:76px;border-radius:50%;background:#d4d4d4}
.intro-title{left:486px;top:44px;font-size:29px;font-weight:700;color:var(--blue)}
.intro-lead{left:486px;top:98px;width:620px;font-size:19px;line-height:27px;color:#444;font-family:"Montserrat",sans-serif}
.intro-label{left:486px;top:172px;font-size:19px;font-weight:700;color:var(--teal)}
.intro-list{left:486px;top:218px;list-style:none;font-family:"Montserrat",sans-serif;font-size:15px;color:#555}
.intro-list li{height:31px;padding-left:22px;position:relative}
.intro-list li::before{content:"";position:absolute;left:2px;top:7px;width:6px;height:6px;border-radius:50%;background:#999}

/* advanced oxidation */
.ao-title{left:97px;top:1068px;font-size:29px;font-weight:700;color:var(--blue)}
.ao-copy{left:97px;top:1128px;width:540px;font-size:15px;line-height:26px;color:#555}
.ao-copy p{margin-bottom:26px}
.ao-copy p.tight{margin-bottom:0}
.ao-figure{left:650px;top:1074px;width:451px;height:400px;background:radial-gradient(circle at 45% 45%,#a9c9cc 0%,#7eaab0 60%,#5f8f98 100%)}
.btn-pill{left:103px;top:1441px;width:132px;height:41px;border-radius:21px;background:var(--blue);color:var(--white);font-size:13px;font-weight:600;text-align:center;line-height:41px}

/* solutions */
.solutions{left:0;top:1548px;width:1200px;height:683px;background:linear-gradient(180deg,#1b1c3a 0%,#2a2a4e 45%,#4a3b52 75%,#2a2640 100%)}
.sol-title{left:0;width:1200px;top:52px;text-align:center;color:var(--white);font-size:29px;font-weight:700}
.card{top:150px;width:239px}
.card-photo{width:239px;height:195px;border:2px solid rgba(255,255,255,.7)}
.card h3{margin-top:30px;text-align:center;color:var(--white);font-size:15px;font-weight:700;line-height:24px;height:48px}
.card p{margin-top:4px;text-align:center;color:#e6e6e6;font-size:12px;line-height:20px;height:126px;padding:0 4px}
.card .btn{margin:18px auto 0;width:152px;height:34px;line-height:34px;text-align:center;background:var(--teal);color:var(--white);font-size:11px;font-weight:600}
.card .btn.primary{background:var(--blue)}

/* partners */
.partners-title{left:0;width:1200px;top:2268px;text-align:center;color:var(--blue);font-size:29px;font-weight:700}
.partner{top:2362px;width:200px;text-align:center}
.partner-mark{height:130px;display:flex;align-items:center;justify-content:center;font-family:"Open Sans",sans-serif;font-weight:700;color:var(--blue);font-size:19px}
.partner-badge{width:124px;height:124px;border-radius:50%}
.partner p{margin-top:26px;font-size:15px;line-height:21px;color:#333;font-family:"Montserrat",sans-serif}

/* footer */
.footer{left:0;top:2649px;width:1200px;height:387px;background:var(--footer)}
.foot-title{color:var(--white);font-size:21px;font-weight:600}
.field{background:var(--field);color:#888;font-size:13px;font-style:italic;padding:8px 14px}
.send{left:356px;top:300px;width:488px;height:49px;background:var(--teal);color:var(--white);font-weight:700;font-size:19px;text-align:center;line-height:49px;font-family:"Montserrat",sans-serif}
.addr-rule{left:873px;top:102px;width:230px;height:1px;background:#333}
.addr{left:873px;top:120px;color:#bbb;font-size:13px;line-height:19px}
.social{top:305px;width:30px;height:30px}
.bottom{left:0;top:3036px;width:1200px;height:51px;background:var(--footer-deep);color:#ccc;font-size:12px;text-align:center;line-height:51px}
</style>
</head>
<body>

<header class="abs hero">
  <div class="hero-photo" role="img" aria-label="Water treatment clarifier basin with blue steel walkway under a pale sky"></div>
  <div class="abs hero-brand"><span class="dot"></span>Velquara</div>
  <h1 class="abs hero-title">
    <span>ADVANCED OXIDATION</span><br>
    <span>SCIENCE FOR ENVIRONMENTAL</span><br>
    <span>POLLUTION MANAGEMENT</span>
  </h1>
  <div class="abs hero-arrow" style="left:26px">
    <svg width="38" height="38" viewBox="0 0 38 38"><path d="M22 12l-7 7 7 7" fill="none" stroke="#fff" stroke-width="2.5"/></svg>
  </div>
  <div class="abs hero-arrow" style="left:1136px">
    <svg width="38" height="38" viewBox="0 0 38 38"><path d="M16 12l7 7-7 7" fill="none" stroke="#fff" stroke-width="2.5"/></svg>
  </div>
</header>

<nav class="abs nav">
  <div class="abs nav-mark" aria-label="Velquara"></div>
  <div class="abs nav-menu">
    <a href="#" style="left:605px">HOME</a>
    <a href="#" style="left:695px">TECHNOLOGY</a>
    <a href="#" style="left:837px">PRODUCTS</a>
    <a href="#" style="left:957px">CONTACT</a>
  </div>
  <div class="abs nav-sep"></div>
  <svg class="abs" style="left:1076px;top:32px" width="22" height="22" viewBox="0 0 22 22"><circle cx="9" cy="9" r="6.5" fill="none" stroke="#fff" stroke-width="2.5"/><path d="M14 14l6 6" stroke="#fff" stroke-width="2.8" stroke-linecap="round"/></svg>
</nav>

<section class="abs intro">
  <div class="abs intro-brand"><span class="dot"></span>Velquara</div>
  <h2 class="abs head intro-title">NEW IDEAS FOR A CLEANER WORLD</h2>
  <p class="abs intro-lead">Environmental pollution control solutions employing nature's most reactive Free Radical</p>
  <h3 class="abs head intro-label">SOLUTIONS:</h3>
  <ul class="abs intro-list">
    <li>WATER</li>
    <li>AIR</li>
    <li>FUEL</li>
  </ul>
</section>

<section>
  <h2 class="abs head ao-title">ADVANCED OXIDATION</h2>
  <div class="abs ao-copy">
    <p>Advanced Oxidation refers to a variety of techniques employing the Hydroxyl Radical, an energetic, highly reactive cousin of the water molecule:</p>
    <p class="tight">To add oxygen to inorganic molecules</p>
    <p>To remove hydrogen from organic molecules</p>
    <p>These transformations convert important industrial contaminants into reactive forms that can be captured or that disintegrate into harmless end products.</p>
  </div>
  <div class="abs ao-figure" role="img" aria-label="Reaction diagram of the hydroxyl radical linked to oxidised molecules on a teal background"></div>
  <div class="abs btn-pill">Read More</div>
</section>

<section class="abs solutions">
  <h2 class="abs head sol-title">SOLUTIONS</h2>

  <article class="abs card" style="left:99px">
    <div class="card-photo" role="img" aria-label="Refinery towers and pipework in grey tones" style="background:linear-gradient(160deg,#cfd3d6,#6c7378 60%,#2e3236)"></div>
    <h3>Fuel Oil Desulfurization</h3>
    <p>Our proprietary low temperature and pressure advanced oxidation catalytic process reliably removes sulfur from diesel transportation fuel at less than half the operating costs of older hydro-desulfurization processes.</p>
    <div class="btn primary">LEARN MORE</div>
  </article>

  <article class="abs card" style="left:354px">
    <div class="card-photo" role="img" aria-label="Worker handling chemical drums in an industrial plant" style="background:linear-gradient(160deg,#8aa0b8,#3d5a7c 55%,#1f3146)"></div>
    <h3>Volatile Organic Compunds (VOC)</h3>
    <p>Alkanes, alkenes, halogenated hydrocarbons, aromatic hydrocarbons, esters, aldehydes, polycyclic aromatic hydrocarbons. We convert these by-products of industrial processes before they enter the atmosphere and cause smog</p>
    <div class="btn">LEARN MORE</div>
  </article>

  <article class="abs card" style="left:609px">
    <div class="card-photo" role="img" aria-label="Smokestacks releasing exhaust against a grey sky" style="background:linear-gradient(180deg,#e4e6e8,#9ea4aa 55%,#2c2f33)"></div>
    <h3>Flue Gas Scrubbing</h3>
    <p>Desulfurization and denitrification using our proprietary flue gas advanced oxidation catalytic process (FGAOC). Sulfur and nitrogen are oxidized and adsorbed into an environmentally friendly solid medium for safe removal from site.</p>
    <div class="btn">LEARN MORE</div>
  </article>

  <article class="abs card" style="left:862px">
    <div class="card-photo" role="img" aria-label="Wastewater outfall pipe discharging into a green riverbank" style="background:linear-gradient(180deg,#6f8f4a,#8b7a5a 55%,#5e6b52)"></div>
    <h3>Wastewater Treatment</h3>
    <p>Photoelectrocatalysed (PEC) anodic oxidation removes soluble organics. Novel anode design using our proprietary nano-carbon surface operates non-selectively to remove 99% of contaminants across a wide range of chemical oxygen demand.</p>
    <div class="btn">LEARN MORE</div>
  </article>
</section>

<section>
  <h2 class="abs head partners-title">PARTNERS</h2>
  <div class="abs partner" style="left:248px">
    <div class="partner-mark">Velquara Systems</div>
    <p>Our sales partner in<br>China</p>
  </div>
  <div class="abs partner" style="left:415px">
    <div class="partner-mark">Kestrel Build</div>
    <p>Our construction<br>partner in China</p>
  </div>
  <div class="abs partner" style="left:590px">
    <div class="partner-mark"><div class="partner-badge" style="background:#1f5a9e" role="img" aria-label="Technology partner badge"></div></div>
    <p>Our technology<br>partner in China</p>
  </div>
  <div class="abs partner" style="left:752px">
    <div class="partner-mark"><div class="partner-badge" style="background:#b3263a" role="img" aria-label="Technology partner badge"></div></div>
    <p>Our technology<br>partner in China</p>
  </div>
</section>

<footer class="abs footer">
  <h3 class="abs foot-title head" style="left:101px;top:60px">Contact form</h3>
  <div class="abs field" style="left:99px;top:121px;width:230px;height:33px">name</div>
  <div class="abs field" style="left:99px;top:181px;width:230px;height:33px">e-mail</div>
  <div class="abs field" style="left:99px;top:241px;width:230px;height:33px">phone</div>
  <div class="abs field" style="left:356px;top:121px;width:488px;height:153px">Comment</div>
  <div class="abs send">SEND</div>

  <h3 class="abs foot-title head" style="left:873px;top:60px">Address</h3>
  <div class="abs addr-rule"></div>
  <div class="abs addr">
    Velquara Corporation, Riverton<br>New Jersey, U.S.A<br><br><br>
    Call +1 555 010 4420<br>
    info@velquaresearch.example
  </div>
  <div class="abs social" style="left:870px;background:#3b5998" role="img" aria-label="Social network link"></div>
  <div class="abs social" style="left:908px;background:#d34836" role="img" aria-label="Social network link"></div>
  <div class="abs social" style="left:946px;background:#2aa3d8" role="img" aria-label="Social network link"></div>
</footer>

<div class="abs bottom">© 2016 yoursite, All Rights reserved</div>
<svg class="abs" style="left:1078px;top:3052px" width="16" height="18" viewBox="0 0 16 18"><path d="M8 2v14M2 8l6-6 6 6" fill="none" stroke="#fff" stroke-width="2.5"/></svg>

</body>
</html>
```